Harborline Auto LLC

Car Dealer Customer Service
Address: 2874 Cresthaven Road, Shelbyville, TN 37162
web: www.harborlineautoxq.net
email: harborlineautoxq@mailnest.example
Phone: (931) 555-0148
Phone: (629) 555-0173

```html
<!DOCTYPE html>
<html lang="en">
<head>
<meta charset="utf-8">
<title>Harborline Auto LLC — Business Card</title>
<link href="https://fonts.googleapis.com/css2?family=Montserrat:wght@500;600;800&display=swap" rel="stylesheet">
<style>
  :root {
    --backdrop: #3b3b3b;
    --card: #181818;
    --brand-blue: #1f80c2;
    --tag-blue: #2b91d3;
    --accent-gold: #efb23e;
    --text-light: #ececec;
  }
  * { box-sizing: border-box; margin: 0; padding: 0; }
  html, body {
    width: 1200px; height: 801px; overflow: hidden;
    background: var(--backdrop);
    font-family: "Montserrat", Arial, sans-serif;
  }
  .stage {
    width: 1200px; height: 801px;
    display: flex; align-items: center; justify-content: center; gap: 40px;
  }
  .card {
    position: relative;
    width: 560px; height: 320px;
    background: var(--card);
    border-bottom: 3px solid var(--brand-blue);
    box-shadow: 0 12px 30px rgba(0,0,0,.35);
  }

  /* Info side */
  .card-info .brand {
    position: absolute; top: 38px; left: 0; right: 0;
    display: flex; align-items: center; justify-content: center; gap: 12px;
  }
  .brand-dot {
    width: 46px; height: 46px; border-radius: 50%;
    background: var(--brand-blue);
  }
  .brand-name {
    font-weight: 800; font-size: 22px; letter-spacing: 1px;
    color: var(--brand-blue); text-transform: uppercase;
  }
  .tagline-row {
    position: absolute; top: 140px; left: 30px; right: 30px;
    display: flex; align-items: center; gap: 14px;
  }
  .tagline-rule { flex: 1; height: 1.5px; background: var(--accent-gold); }
  .tagline {
    font-weight: 600; font-size: 17px; color: var(--tag-blue);
    text-transform: uppercase; white-space: nowrap;
  }
  .contact-list {
    position: absolute; left: 40px; bottom: 42px;
    list-style: none; display: flex; flex-direction: column; gap: 6px;
  }
  .contact-list li {
    display: flex; align-items: center; gap: 9px;
    font-size: 13px; font-weight: 500; color: var(--text-light);
  }
  .contact-list svg { width: 12px; height: 12px; fill: var(--accent-gold); flex: none; }
  .address {
    position: absolute; right: 40px; bottom: 42px;
    font-style: normal; text-align: right;
    font-size: 13px; font-weight: 500; color: var(--text-light); line-height: 1.55;
  }
  .address .web { color: var(--accent-gold); font-weight: 600; }

  /* Brand side */
  .card-brand {
    display: flex; flex-direction: column; align-items: center; justify-content: center; gap: 22px;
  }
  .card-brand .brand-dot { width: 90px; height: 90px; }
  .card-brand .brand-name { font-size: 38px; letter-spacing: 2px; }
</style>
</head>
<body>
<main class="stage">
  <section class="card card-info" aria-label="Business card, contact side">
    <div class="brand">
      <span class="brand-dot" aria-hidden="true"></span>
      <span class="brand-name">Harborline Auto</span>
    </div>
    <div class="tagline-row">
      <span class="tagline-rule"></span>
      <h2 class="tagline">Car Dealer Customer Service</h2>
      <span class="tagline-rule"></span>
    </div>
    <ul class="contact-list">
      <li>
        <svg viewBox="0 0 24 24" aria-hidden="true"><path d="M6.6 10.8a15.1 15.1 0 0 0 6.6 6.6l2.2-2.2a1 1 0 0 1 1-.25 11.4 11.4 0 0 0 3.6.57 1 1 0 0 1 1 1V20a1 1 0 0 1-1 1A17 17 0 0 1 3 4a1 1 0 0 1 1-1h3.5a1 1 0 0 1 1 1c0 1.25.2 2.45.57 3.57a1 1 0 0 1-.25 1z"/></svg>
        (931) 555-0148
      </li>
      <li>
        <svg viewBox="0 0 24 24" aria-hidden="true"><path d="M6.6 10.8a15.1 15.1 0 0 0 6.6 6.6l2.2-2.2a1 1 0 0 1 1-.25 11.4 11.4 0 0 0 3.6.57 1 1 0 0 1 1 1V20a1 1 0 0 1-1 1A17 17 0 0 1 3 4a1 1 0 0 1 1-1h3.5a1 1 0 0 1 1 1c0 1.25.2 2.45.57 3.57a1 1 0 0 1-.25 1z"/></svg>
        (629) 555-0173
      </li>
      <li>
        <svg viewBox="0 0 24 24" aria-hidden="true"><path d="M2 5h20v14H2z M2 5l10 8 10-8" /></svg>
        harborlineautoxq@mailnest.example
      </li>
    </ul>
    <address class="address">
      2874 Cresthaven Road<br>
      Shelbyville, TN 37162<br>
      <span class="web">www.harborlineautoxq.net</span>
    </address>
  </section>

  <section class="card card-brand" aria-label="Business card, brand side">
    <span class="brand-dot" aria-hidden="true"></span>
    <h1 class="brand-name">Harborline Auto</h1>
  </section>
</main>
</body>
</html>
```